Trucking Company Website Design

We are working with a Trucking company in California. They provide trucking services for dirt, gravel, landscape bark, and landscape materials.

As you might imagine, there are no websites we could find for inspiration for trucking companies.

Thank you for taking the time to consider designing a website for us. We are web developers based in Stockton, CA, USA. Most of our projects go through the same process. Understanding this process may help you win a project with us. We custom-code all of our websites in-house. We don’t have any requirements as to what tools you use for your design, but we ask that you follow these guidelines.

IMAGES:
If you use any images or icons in the design, we ask that you have a link to the asset so we can purchase the image/icon. Most of the designs we submit do not have the customer’s images on them unless they have some great images. Be creative; show us the feeling you are trying to portray with your image choices. Use any royalty-free site you choose. We subscribe to Quillo and mainly use their images, but we can purchase images outside of Quillo. PLEASE NOTE: we will not submit designs to clients with watermarks on the images.

FONTS:
We ask that you identify the fonts you’re using in the design. This can be done in a message if you want. We typically use Varnex Fonts and Quillo Fonts.

CONTENT:
We're always open to different content and ideas. We often submit designs with stock images so the client can see our vision. We typically take pictures after the website launch to use their images with our vision. Lorem Ipsum is fine for paragraphs, but we ask that you make the Headers with correct English. We want to be able to show the vision and identify the sections of the website.

INSPIRATION:
We typically add a couple of links in the brief of websites we like to help you get started in your design.

REVISIONS:
We do not often ask for revisions of the designs unless we see something in the design that may not appeal to the client. If there are slight changes that we want to make, we do that in the development process.

FEEDBACK:
We rarely give feedback on designs during the design process. We are working on many website projects and do not have the time to provide feedback. We usually respond if your request is well thought out and asks specific questions, but a note asking “feedback, please” usually goes unanswered.

```html
<!DOCTYPE html>
<html lang="en">
<head>
<meta charset="utf-8">
<title>Ridgeline Haulage — Trucking Services</title>
<link href="https://fonts.googleapis.com/css2?family=Poppins:wght@400;500;600;700;800&display=swap" rel="stylesheet">
<style>
:root{
  --blue:#1b78b9;
  --blue-deep:#125d93;
  --red:#e91e3f;
  --ink:#111820;
  --night:#0b1119;
  --text:#333a42;
  --muted:#6b7480;
  --line:#d9dee4;
  --white:#ffffff;
}
*{box-sizing:border-box;margin:0;padding:0}
html,body{width:1200px;height:4008px;overflow:hidden}
body{font-family:'Poppins',sans-serif;color:var(--text);background:var(--white);position:relative}
.abs{position:absolute}

/* header */
.topbar{left:0;top:0;width:1200px;height:64px;background:var(--night);z-index:5}
.brand{left:0;top:0;width:420px;height:64px;background:var(--blue);clip-path:polygon(0 0,100% 0,92% 100%,0 100%);z-index:6;display:flex;align-items:center;padding-left:110px;gap:10px}
.brand-name{color:var(--white);font-weight:700;font-size:22px;letter-spacing:1px;line-height:1}
.brand-mark{width:18px;height:18px;background:var(--red)}
.nav{right:40px;top:0;height:64px;display:flex;align-items:center;gap:44px;z-index:6}
.nav a{color:var(--white);text-decoration:none;font-size:17px;font-weight:500}
.nav a.active{color:var(--red);border-bottom:2px solid var(--red);padding-bottom:2px}

/* hero */
.hero{left:0;top:0;width:1200px;height:664px;background:linear-gradient(180deg,#2a323a 0%,#4c5258 45%,#2b2b2e 80%,#1a1a1c 100%);clip-path:polygon(0 0,100% 0,100% 560px,1110px 664px,90px 664px,0 560px)}
.hero-outline{left:0;top:0;z-index:2}
.hero-title{left:0;top:270px;width:1200px;text-align:center;z-index:3;color:var(--white)}
.hero-title .small{font-size:52px;font-weight:500;letter-spacing:1px;line-height:1.1}
.hero-title .big{font-size:66px;font-weight:700;line-height:1.15}
.hero-title .big .b{color:var(--blue)}
.hero-title .big .r{color:var(--red)}
.btn{display:inline-flex;align-items:center;gap:14px;background:var(--blue-deep);color:var(--white);font-weight:600;font-size:17px;border-radius:30px;padding:0 6px 0 26px;height:52px;text-decoration:none}
.btn .arr{width:40px;height:40px;border-radius:50%;background:var(--red);display:flex;align-items:center;justify-content:center}
.hero-btn{left:505px;top:438px;z-index:3}
.slide-arrow{width:40px;height:40px;border-radius:50%;border:2px solid var(--white);display:flex;align-items:center;justify-content:center;z-index:3}

/* section heading */
.heading{font-size:32px;font-weight:700;display:flex;align-items:center;gap:10px;letter-spacing:.5px}
.heading .chev{width:14px;height:22px}

/* about */
.about-head{left:112px;top:740px;color:var(--blue)}
.about-text{left:112px;top:796px;width:470px;font-size:16px;line-height:1.55;color:var(--text)}
.about-text p+p{margin-top:18px}
.about-btn{left:112px;top:1048px}
.about-frame{left:650px;top:756px;width:450px;height:340px;z-index:0}
.about-photo{left:640px;top:770px;width:436px;height:320px;background:linear-gradient(135deg,#3b4a5a,#7d8a96 55%,#c9ccd0);z-index:1}

/* services */
.services{left:0;top:1190px;width:1200px;height:830px;background:linear-gradient(180deg,var(--blue) 0%,#2a86c4 50%,var(--blue) 100%)}
.services-head{left:0;top:1236px;width:1200px;justify-content:center;color:var(--white)}
.svc{width:324px;height:300px}
.svc-img{position:absolute;inset:0;clip-path:polygon(0 0,100% 0,100% 100%,12% 100%,0 88%)}
.svc-tag{position:absolute;left:50%;bottom:-4px;transform:translateX(-50%);background:var(--white);color:var(--ink);font-weight:700;font-size:13px;padding:8px 26px;white-space:nowrap;letter-spacing:.5px;clip-path:polygon(8% 0,100% 0,92% 100%,0 100%)}

/* blog */
.blog-head{left:0;top:2104px;width:1200px;justify-content:center;color:var(--blue)}
.post{width:304px;height:424px;background:var(--white);border:1px solid var(--line);box-shadow:0 4px 14px rgba(0,0,0,.08)}
.post-img{position:absolute;left:0;top:0;width:304px;height:220px}
.post-date{position:absolute;right:0;top:0;width:52px;height:58px;background:var(--red);color:var(--white);text-align:center;font-weight:700;font-size:22px;line-height:1;padding-top:9px}
.post-date small{display:block;font-size:11px;font-weight:500;margin-top:4px}
.post-label{position:absolute;left:0;top:220px;background:var(--blue);color:var(--white);font-size:14px;font-weight:700;padding:8px 14px}
.post-text{position:absolute;left:14px;top:268px;width:276px;font-size:14px;line-height:1.5;color:var(--text)}
.post-arr{position:absolute;right:16px;bottom:16px}
.round-arrow{width:36px;height:36px;border-radius:50%;border:2px solid #555;display:flex;align-items:center;justify-content:center}

/* testimonials */
.testi{left:0;top:2700px;width:1200px;height:380px;background:linear-gradient(180deg,var(--blue-deep),var(--blue))}
.testi-head{left:0;top:2748px;width:1200px;justify-content:center;color:var(--white)}
.testi-text{left:180px;top:2804px;width:840px;text-align:center;color:var(--white);font-size:15px;line-height:1.55}
.avatar{left:560px;top:2912px;width:80px;height:80px;border-radius:50%;background:linear-gradient(135deg,#8d9aa6,#dfe3e7);border:3px solid var(--white)}
.testi-name{left:0;top:3004px;width:1200px;text-align:center;color:var(--white);font-weight:600;font-size:16px}

/* contact */
.contact{left:112px;top:3160px;width:976px;height:380px;background:var(--white);border:1px solid var(--line);border-radius:6px;box-shadow:0 4px 16px rgba(0,0,0,.08)}
.contact-head{left:0;top:3200px;width:1200px;text-align:center;font-size:36px;font-weight:700;color:var(--ink)}
.contact-item{top:3296px;display:flex;align-items:center;gap:22px;font-size:16px;color:var(--text)}
.ci-icon{width:44px;height:44px;border-radius:6px;background:var(--blue);display:flex;align-items:center;justify-content:center}
.contact-btn{left:500px;top:3374px}

/* footer */
.footer{left:0;top:3600px;width:1200px;height:408px;background:#000;clip-path:polygon(0 60px,90px 0,1110px 0,1200px 60px,1200px 408px,0 408px)}
.footer-outline{left:0;top:3600px}
.footer-brand{left:0;top:3650px;width:1200px;display:flex;justify-content:center;align-items:center;gap:12px}
.footer-brand .brand-name{font-size:34px}
.footer-brand .brand-mark{width:26px;height:26px}
.social{left:0;top:3770px;width:1200px;display:flex;justify-content:center;gap:14px}
.social span{width:28px;height:28px;background:var(--white);border-radius:4px}
.footer-nav{left:0;top:3840px;width:1200px;display:flex;justify-content:center;gap:70px}
.footer-nav a{color:var(--white);text-decoration:none;font-size:20px;font-weight:600}
.subscribe{left:430px;top:3892px;width:340px;height:42px;display:flex}
.subscribe .field{flex:1;background:var(--white);color:#222;font-size:14px;display:flex;align-items:center;padding-left:16px}
.subscribe .send{width:48px;background:var(--red);display:flex;align-items:center;justify-content:center}
.copyright{left:0;top:3964px;width:1200px;height:44px;border-top:1px solid #333;color:var(--white);font-size:15px;display:flex;align-items:center;justify-content:center}
</style>
</head>
<body>

<!-- hero -->
<div class="abs hero" role="img" aria-label="Loaded dump truck being filled by an excavator at a quarry at dusk"></div>
<svg class="abs hero-outline" width="1200" height="680" viewBox="0 0 1200 680">
  <polyline points="0,560 90,664 1110,664 1200,560" fill="none" stroke="#e91e3f" stroke-width="5"/>
</svg>

<header>
  <div class="abs topbar"></div>
  <div class="abs brand"><span class="brand-name">RIDGELINE HAULAGE</span><span class="brand-mark"></span></div>
  <nav class="abs nav">
    <a href="#" class="active">Home</a><a href="#">About Us</a><a href="#">Services</a><a href="#">Testimonials</a><a href="#">Contact us</a>
  </nav>
</header>

<div class="abs hero-title">
  <div class="small">WELCOME TO</div>
  <div class="big"><span class="b">RIDGELINE</span> <span class="r">HAULAGE</span></div>
</div>
<a class="abs btn hero-btn" href="#">GET STARTED <span class="arr"><svg width="18" height="14" viewBox="0 0 18 14"><path d="M1 7h15M10 1l6 6-6 6" stroke="#fff" stroke-width="2.4" fill="none"/></svg></span></a>
<div class="abs slide-arrow" style="left:20px;top:300px"><svg width="14" height="14" viewBox="0 0 14 14"><path d="M9 2L4 7l5 5" stroke="#fff" stroke-width="2.4" fill="none"/></svg></div>
<div class="abs slide-arrow" style="left:1140px;top:300px"><svg width="14" height="14" viewBox="0 0 14 14"><path d="M5 2l5 5-5 5" stroke="#fff" stroke-width="2.4" fill="none"/></svg></div>

<!-- about -->
<h2 class="abs heading about-head">ABOUT US <svg class="chev" viewBox="0 0 14 22"><path d="M0 0h6l8 11-8 11H0l8-11z" fill="#e91e3f"/></svg></h2>
<div class="abs about-text">
  <p>Lorem ipsum dolor sit amet, consectetur adipiscing elit, sed do eiusmod tempor incididunt ut labore et dolore magna aliqua. Ut enim ad minim veniam, quis nostrud exercitation ullamco laboris nisi ut aliquip ex ea commodo consequat.</p>
  <p>Duis aute irure dolor in reprehenderit in voluptate velit esse cillum dolore eu fugiat nulla pariatur. Excepteur sint occaecat cupidatat non proident, sunt in culpa qui officia deserunt mollit anim id est laborum.</p>
</div>
<a class="abs btn about-btn" href="#">READ MORE <span class="arr"><svg width="18" height="14" viewBox="0 0 18 14"><path d="M1 7h15M10 1l6 6-6 6" stroke="#fff" stroke-width="2.4" fill="none"/></svg></span></a>
<svg class="abs about-frame" width="450" height="340" viewBox="0 0 450 340" style="left:650px;top:756px">
  <polyline points="40,2 420,2 448,30 448,338" fill="none" stroke="#e91e3f" stroke-width="5"/>
</svg>
<div class="abs about-photo" role="img" aria-label="Two colleagues reviewing a laptop in an office"></div>

<!-- services -->
<section>
  <div class="abs services" role="img" aria-label="Faded construction site backdrop in blue tones"></div>
  <h2 class="abs heading services-head">SERVICES <svg class="chev" viewBox="0 0 14 22"><path d="M0 0h6l8 11-8 11H0l8-11z" fill="#e91e3f"/></svg></h2>
  <div class="abs svc" style="left:208px;top:1320px"><div class="svc-img" role="img" aria-label="Dump truck unloading dirt" style="background:linear-gradient(160deg,#8fb2d6,#3d5f8a 55%,#6b5a45)"></div><div class="svc-tag">DIRT</div></div>
  <div class="abs svc" style="left:672px;top:1320px"><div class="svc-img" role="img" aria-label="Orange dump truck loaded with gravel" style="background:linear-gradient(160deg,#c9d2da,#d9772d 50%,#4a4440)"></div><div class="svc-tag">GRAVEL</div></div>
  <div class="abs svc" style="left:208px;top:1648px"><div class="svc-img" role="img" aria-label="Truck carrying landscape bark" style="background:linear-gradient(160deg,#e9b27c,#b8693a 55%,#7a4a2a)"></div><div class="svc-tag">LANDSCAPE BARK</div></div>
  <div class="abs svc" style="left:672px;top:1648px"><div class="svc-img" role="img" aria-label="Trucks hauling landscape materials at a yard" style="background:linear-gradient(160deg,#9aa3ab,#545a60 55%,#2e3034)"></div><div class="svc-tag">LANDSCAPE MATERIALS</div></div>
</section>

<!-- blog -->
<section>
  <h2 class="abs heading blog-head">BLOG <svg class="chev" viewBox="0 0 14 22"><path d="M0 0h6l8 11-8 11H0l8-11z" fill="#e91e3f"/></svg></h2>
  <div class="abs round-arrow" style="left:22px;top:2370px"><svg width="12" height="12" viewBox="0 0 14 14"><path d="M9 2L4 7l5 5" stroke="#555" stroke-width="2.4" fill="none"/></svg></div>
  <div class="abs round-arrow" style="left:1112px;top:2370px"><svg width="12" height="12" viewBox="0 0 14 14"><path d="M5 2l5 5-5 5" stroke="#555" stroke-width="2.4" fill="none"/></svg></div>

  <article class="abs post" style="left:112px;top:2180px">
    <div class="post-img" role="img" aria-label="Road paving crew with rollers at sunset" style="background:linear-gradient(180deg,#f0a060,#c45f3a 45%,#3a3a3e)"></div>
    <div class="post-date">10<small>Nov</small></div>
    <div class="post-label">LOREM IPSUM</div>
    <p class="post-text">Lorem ipsum dolor sit amet, consectetur adipiscing elit, sed do eiusmod tempor incididunt ut labore et dolore magna aliqua.</p>
    <svg class="post-arr" width="22" height="14" viewBox="0 0 22 14"><path d="M1 7h19M14 1l6 6-6 6" stroke="#222" stroke-width="2.2" fill="none"/></svg>
  </article>
  <article class="abs post" style="left:448px;top:2180px">
    <div class="post-img" role="img" aria-label="Yellow loader working at a construction site" style="background:linear-gradient(180deg,#8fc3e8,#d9b13a 55%,#8a7a5a)"></div>
    <div class="post-date">20<small>Nov</small></div>
    <div class="post-label">LOREM IPSUM</div>
    <p class="post-text">Lorem ipsum dolor sit amet, consectetur adipiscing elit, sed do eiusmod tempor incididunt ut labore et dolore magna aliqua.</p>
    <svg class="post-arr" width="22" height="14" viewBox="0 0 22 14"><path d="M1 7h19M14 1l6 6-6 6" stroke="#222" stroke-width="2.2" fill="none"/></svg>
  </article>
  <article class="abs post" style="left:784px;top:2180px">
    <div class="post-img" role="img" aria-label="Red truck loaded with gravel on a dirt road" style="background:linear-gradient(180deg,#a9c6de,#b23a3a 50%,#9b8c70)"></div>
    <div class="post-date">20<small>Nov</small></div>
    <div class="post-label">LOREM IPSUM</div>
    <p class="post-text">Lorem ipsum dolor sit amet, consectetur adipiscing elit, sed do eiusmod tempor incididunt ut labore et dolore magna aliqua.</p>
    <svg class="post-arr" width="22" height="14" viewBox="0 0 22 14"><path d="M1 7h19M14 1l6 6-6 6" stroke="#222" stroke-width="2.2" fill="none"/></svg>
  </article>
</section>

<!-- testimonials -->
<section>
  <div class="abs testi"></div>
  <h2 class="abs heading testi-head">TESTIMONIALS <svg class="chev" viewBox="0 0 14 22"><path d="M0 0h6l8 11-8 11H0l8-11z" fill="#e91e3f"/></svg></h2>
  <p class="abs testi-text">Lorem ipsum dolor sit amet, consectetur adipiscing elit, sed do eiusmod tempor incididunt ut labore et dolore magna aliqua. Ut enim ad minim veniam, quis nostrud exercitation ullamco laboris nisi ut aliquip ex ea commodo consequat.</p>
  <div class="abs slide-arrow" style="left:20px;top:2852px"><svg width="14" height="14" viewBox="0 0 14 14"><path d="M9 2L4 7l5 5" stroke="#fff" stroke-width="2.4" fill="none"/></svg></div>
  <div class="abs slide-arrow" style="left:1140px;top:2852px"><svg width="14" height="14" viewBox="0 0 14 14"><path d="M5 2l5 5-5 5" stroke="#fff" stroke-width="2.4" fill="none"/></svg></div>
  <div class="abs avatar" role="img" aria-label="Portrait of the client giving the testimonial"></div>
  <div class="abs testi-name">Marcus T.L</div>
</section>

<!-- contact -->
<section>
  <div class="abs contact"></div>
  <h2 class="abs contact-head">Do you have any questions?</h2>
  <div class="abs contact-item" style="left:136px"><span class="ci-icon"><svg width="20" height="20" viewBox="0 0 20 20"><circle cx="10" cy="6" r="4" fill="#fff"/><path d="M2 19c0-5 4-7 8-7s8 2 8 7z" fill="#fff"/></svg></span>Lorem Ipsum</div>
  <div class="abs contact-item" style="left:460px"><span class="ci-icon"><svg width="20" height="20" viewBox="0 0 20 20"><path d="M4 1l4 4-2 3c1 3 3 5 6 6l3-2 4 4-3 3C8 19 1 12 1 4z" fill="#fff"/></svg></span>+1 555 010 2040</div>
  <div class="abs contact-item" style="left:760px"><span class="ci-icon"><svg width="22" height="16" viewBox="0 0 22 16"><rect x="1" y="1" width="20" height="14" fill="none" stroke="#fff" stroke-width="2"/><path d="M1 1l10 8 10-8" fill="none" stroke="#fff" stroke-width="2"/></svg></span>info@ridgelinehaulage.com</div>
  <a class="abs btn contact-btn" href="#">CONTACT US <span class="arr"><svg width="18" height="14" viewBox="0 0 18 14"><path d="M1 7h15M10 1l6 6-6 6" stroke="#fff" stroke-width="2.4" fill="none"/></svg></span></a>
</section>

<!-- footer -->
<footer>
  <div class="abs footer"></div>
  <svg class="abs footer-outline" width="1200" height="70" viewBox="0 0 1200 70">
    <polyline points="0,60 90,2 1110,2 1200,60" fill="none" stroke="#e91e3f" stroke-width="5"/>
  </svg>
  <div class="abs footer-brand"><span class="brand-name">RIDGELINE HAULAGE</span><span class="brand-mark"></span></div>
  <div class="abs social"><span></span><span></span><span></span><span></span></div>
  <nav class="abs footer-nav"><a href="#">Home</a><a href="#">About Us</a><a href="#">Services</a><a href="#">Testimonials</a><a href="#">Contact Us</a></nav>
  <div class="abs subscribe"><div class="field">Enter your email</div><div class="send"><svg width="22" height="16" viewBox="0 0 22 16"><rect x="1" y="1" width="20" height="14" fill="none" stroke="#fff" stroke-width="2"/><path d="M1 1l10 8 10-8" fill="none" stroke="#fff" stroke-width="2"/></svg></div></div>
  <div class="abs copyright">Copyright © ridgeline haulage. All rights reserved.</div>
</footer>

</body>
</html>
```